Equipment Finance Specialist I work with companies who need the funds to buy their equipment

I would like a business card that stands out on the shelves. I want to be able to hand it to someone and say WOW. This card should have my logo.
You can put color into it I am very open on design and color

What my company does is we deal with dealerships that sell equipment such as Dump Trucks garbage trucks tractors trailers. Customers get referred to us and depending on their time in business we will ask for the following items

Companies that have been in business for more than two years we have a credit application program up to 250K . With this program we need the following items Credit application filled out(which is what I would like to be able for the customer to click on my website to get.) as well as three current month bank statements.

Deals over 250k we will need the following items

2 years business tax returns
2 years personal tax returns
Profit & Loss statement
Personal Financial Statement

what we do
100% FINANCING
SEASONAL PAYMENTS
LOAN BALLOON PAYMENTS
TRAC LEASING
LOW-INTEREST REFINANCING RATES
DEBT CONSOLIDATION

We specialize in creative financing solutions and offer a variety of reliable, flexible and expandable lending choices.

Target Market(s)

Trucking Companies

Industry/Entity Type

Trucking Company

Contact Information for Business Card

* $250,000 Application only Program
* Loans from $30,000 to 5,000,000
* Competitive Interest Rates

Font styles to use
Serif
Sans Serif

Colors

Designer to choose colors to be used in the design.

Requirements
Must have
• On the back of the card.
• * $250,000 Application only Program
• * Loans from $30,000 to 5,000,000
• My name, email, website. address
• * Competitive Interest Rates
• * 100% Financing
Nice to have
• I want my logo to pop on the card
• My logo is the great one I would like to use
Should not have
• I am up for your creativity as well

```html
<!DOCTYPE html>
<html lang="en">
<head>
<meta charset="utf-8">
<title>Ironhaul Finance – Business Card</title>
<link rel="stylesheet" href="https://fonts.googleapis.com/css2?family=Montserrat:wght@400;600;700;800&display=swap">
<style>
  :root {
    --bg: #1b1b1c;
    --carbon: #2b2e31;
    --carbon-dark: #17191b;
    --silver-light: #f4f4f4;
    --silver-mid: #b9b9b9;
    --silver-dark: #6e6e6e;
    --paper: #ffffff;
    --ink: #1e1e1e;
    --ink-soft: #555555;
    --ink-faint: #7a7a7a;
  }
  * { box-sizing: border-box; margin: 0; padding: 0; }
  html, body {
    width: 1200px; height: 1200px; overflow: hidden;
    background: var(--bg);
    font-family: "Montserrat", sans-serif;
  }
  .canvas {
    position: relative; width: 1200px; height: 1200px;
  }
  .card {
    position: absolute; left: 150px; width: 900px; height: 514px;
    background: var(--paper); overflow: hidden;
    box-shadow: 0 18px 40px rgba(0,0,0,.55);
  }
  .card--front { top: 48px; }
  .card--back { top: 638px; }

  /* front */
  .front-art { position: absolute; inset: 0; }
  .brand {
    position: absolute; left: 70px; top: 95px;
    display: flex; align-items: center; gap: 28px;
  }
  .brand-emblem {
    width: 150px; height: 150px; border-radius: 50%;
    background: radial-gradient(circle at 40% 35%, #e6e6e6, #8d8d8d 60%, #4a4a4a);
  }
  .brand-name {
    color: var(--silver-light); font-weight: 800; font-size: 64px;
    line-height: .95; letter-spacing: 1px; text-transform: uppercase;
  }
  .front-url {
    position: absolute; left: 0; right: 0; bottom: 62px;
    text-align: center; font-weight: 800; font-size: 34px; color: var(--ink);
  }

  /* back */
  .back-art { position: absolute; inset: 0; }
  .person {
    position: absolute; left: 60px; top: 120px; width: 380px;
  }
  .person-name { font-weight: 700; font-size: 38px; color: #3a3a3a; }
  .person-title { font-size: 24px; color: var(--ink-faint); margin-top: 6px; }
  .person-address { font-size: 21px; color: var(--ink-faint); margin-top: 34px; line-height: 1.45; }
  .divider {
    position: absolute; left: 450px; top: 80px; width: 2px; height: 190px;
    background: linear-gradient(var(--silver-dark), var(--silver-mid));
  }
  .contacts {
    position: absolute; left: 490px; top: 86px; list-style: none;
  }
  .contacts li {
    display: flex; align-items: center; gap: 18px;
    font-size: 24px; color: var(--ink-soft); height: 52px;
  }
  .contacts svg { width: 22px; height: 22px; fill: #333; flex: none; }
  .offers {
    position: absolute; left: 330px; top: 300px; width: 540px;
    list-style: none; text-align: center;
  }
  .offers li { font-size: 25px; color: var(--ink-soft); line-height: 1.3; }
  .offers strong { font-weight: 800; color: var(--ink); }
</style>
</head>
<body>
<main class="canvas">

  <section class="card card--front" aria-label="Card front">
    <svg class="front-art" viewBox="0 0 900 514" preserveAspectRatio="none" aria-hidden="true">
      <defs>
        <linearGradient id="carbonFill" x1="0" y1="0" x2="0" y2="1">
          <stop offset="0" stop-color="var(--carbon)"/>
          <stop offset="1" stop-color="var(--carbon-dark)"/>
        </linearGradient>
        <linearGradient id="silverSwoosh" x1="0" y1="0" x2="1" y2="0">
          <stop offset="0" stop-color="#8a8a8a"/>
          <stop offset=".35" stop-color="#f5f5f5"/>
          <stop offset=".6" stop-color="#9c9c9c"/>
          <stop offset="1" stop-color="#e8e8e8"/>
        </linearGradient>
      </defs>
      <path d="M0 0H900V250C640 380 280 390 0 340Z" fill="url(#silverSwoosh)"/>
      <path d="M0 0H900V230C640 356 280 362 0 318Z" fill="url(#carbonFill)"/>
    </svg>
    <div class="brand">
      <div class="brand-emblem" role="img" aria-label="Company emblem illustration of a work truck"></div>
      <div class="brand-name">Ironhaul<br>Finance</div>
    </div>
    <p class="front-url">www.yourwebsite.com</p>
  </section>

  <section class="card card--back" aria-label="Card back">
    <svg class="back-art" viewBox="0 0 900 514" preserveAspectRatio="none" aria-hidden="true">
      <defs>
        <linearGradient id="silverBar" x1="0" y1="0" x2="1" y2="0">
          <stop offset="0" stop-color="#7a7a7a"/>
          <stop offset=".45" stop-color="#f7f7f7"/>
          <stop offset=".7" stop-color="#a8a8a8"/>
          <stop offset="1" stop-color="#5e5e5e"/>
        </linearGradient>
      </defs>
      <rect x="0" y="0" width="900" height="42" fill="url(#silverBar)"/>
      <rect x="0" y="456" width="900" height="58" fill="url(#silverBar)"/>
    </svg>

    <div class="person">
      <h1 class="person-name">Your Name</h1>
      <p class="person-title">Your Title</p>
      <p class="person-address">Your Address, City<br>State, Zip 0000, Country</p>
    </div>

    <div class="divider"></div>

    <ul class="contacts">
      <li>
        <svg viewBox="0 0 24 24"><path d="M6.6 10.8a15 15 0 0 0 6.6 6.6l2.2-2.2c.3-.3.7-.4 1-.2 1.1.4 2.3.6 3.6.6.6 0 1 .4 1 1V20c0 .6-.4 1-1 1C10.6 21 3 13.4 3 4c0-.6.4-1 1-1h3.5c.6 0 1 .4 1 1 0 1.3.2 2.5.6 3.6.1.3 0 .7-.2 1z"/></svg>
        (012) 345 6789
      </li>
      <li>
        <svg viewBox="0 0 24 24"><path d="M2 5h20v14H2z M2 5l10 8 10-8" fill="none" stroke="#333" stroke-width="2"/></svg>
        youremail@mailhost.com
      </li>
      <li>
        <svg viewBox="0 0 24 24"><circle cx="12" cy="12" r="9" fill="none" stroke="#333" stroke-width="2"/><path d="M3 12h18M12 3c3 3 3 15 0 18M12 3c-3 3-3 15 0 18" fill="none" stroke="#333" stroke-width="1.6"/></svg>
        www.yourwebsite.com
      </li>
    </ul>

    <ul class="offers">
      <li><strong>$250,000</strong> Application only Program</li>
      <li>Loans from <strong>$30,000 to 5,000,000</strong></li>
      <li>Competitive Interest Rates</li>
      <li><strong>100%</strong> Financing</li>
    </ul>
  </section>

</main>
</body>
</html>
```